PAX

We need to design a power point presentation that can englobe all our company products.

This presentation has to have all the required to be used as template for future presentations.

We focus on prodcut developing for supermarkets, ( we help them with their own brand products ex. Sunny Harvest, TK, etc.)
Also we are on the marine industry, we develop ships and oil rigs for the Oil and deep water market.

Target Market(s)

Oil Companies
Supermarket companies
Retail Companies

Industry/Entity Type

It Company

Requirements
Must have
• Our Logo and company colors
Nice to have
• Something describing globalization.
Should not have
• Orange color

```html
<!DOCTYPE html>
<html lang="en">
<head>
<meta charset="utf-8">
<title>PAX – Presentation Template</title>
<link href="https://fonts.googleapis.com/css2?family=Orbitron:wght@700;900&family=Arimo:wght@400;700&display=swap" rel="stylesheet">
<style>
  :root {
    --blue-deep: #0f2fc4;
    --blue-main: #1d47e0;
    --blue-light: #3d6ef2;
    --map-dark: #0b3c9c;
    --map-mid: #1f66c8;
    --map-light: #5aa6ee;
    --accent-green: #7ed321;
    --heading-green: #6cf02a;
    --white: #ffffff;
    --ring: #0a2a8a;
    --platform: #cfd3d8;
    --platform-side: #9ea4ab;
  }
  html, body {
    margin: 0;
    padding: 0;
    width: 1200px;
    height: 900px;
    overflow: hidden;
  }
  .slide {
    position: relative;
    width: 1200px;
    height: 900px;
    overflow: hidden;
    background: radial-gradient(ellipse at 55% 50%, var(--blue-light) 0%, var(--blue-main) 45%, var(--blue-deep) 100%);
    font-family: "Arimo", Arial, sans-serif;
  }
  .slide-art {
    position: absolute;
    inset: 0;
    width: 1200px;
    height: 900px;
  }
  .project-title {
    position: absolute;
    top: 44px;
    left: 0;
    width: 1188px;
    margin: 0;
    text-align: center;
    font-family: "Orbitron", "Arial Black", sans-serif;
    font-size: 41px;
    font-weight: 900;
    letter-spacing: 3px;
    color: var(--white);
    text-shadow: 0 2px 3px rgba(0,0,0,0.5);
  }
  .brand-tab {
    position: absolute;
    top: 0;
    left: 1008px;
    width: 147px;
    height: 195px;
    background: var(--white);
    border-radius: 0 0 30px 30px;
    box-shadow: 0 3px 8px rgba(0,0,0,0.35);
    display: flex;
    flex-direction: column;
    align-items: center;
    justify-content: center;
    gap: 14px;
  }
  .brand-mark {
    width: 54px;
    height: 54px;
    border-radius: 50%;
    background: var(--accent-green);
  }
  .brand-name {
    font-family: "Orbitron", "Arial Black", sans-serif;
    font-weight: 700;
    font-size: 32px;
    color: var(--accent-green);
  }
  .content {
    position: absolute;
    top: 200px;
    left: 62px;
    width: 860px;
  }
  .content-heading {
    margin: 0 0 12px;
    font-family: "Orbitron", "Arial Black", sans-serif;
    font-size: 29px;
    font-weight: 900;
    letter-spacing: 1px;
    color: var(--heading-green);
  }
  .content-body {
    margin: 0;
    font-size: 22px;
    line-height: 36px;
    color: var(--white);
  }
  .photo {
    position: absolute;
    left: 995px;
    width: 164px;
    height: 164px;
    border-radius: 50%;
    border: 5px solid var(--ring);
    box-shadow: 0 0 0 3px rgba(255,255,255,0.12), 0 4px 10px rgba(0,0,0,0.4);
  }
  .photo-vessels { top: 268px; background: linear-gradient(180deg, #8fb8e0 0%, #cfd8de 45%, #d33a2a 70%, #3a6b9a 100%); }
  .photo-cruise  { top: 478px; background: linear-gradient(180deg, #6fa4df 0%, #dfe9f2 50%, #f4f6f8 62%, #2f6aa6 100%); }
  .photo-rig     { top: 694px; background: linear-gradient(180deg, #1c2530 0%, #4a3a32 55%, #8a5a3c 100%); }
</style>
</head>
<body>
<div class="slide">
  <svg class="slide-art" viewBox="0 0 800 600" preserveAspectRatio="none" xmlns="http://www.w3.org/2000/svg">
    <defs>
      <radialGradient id="mapGlow" cx="0.45" cy="0.3" r="0.7">
        <stop offset="0" stop-color="var(--map-light)"/>
        <stop offset="0.55" stop-color="var(--map-mid)"/>
        <stop offset="1" stop-color="var(--map-dark)"/>
      </radialGradient>
      <clipPath id="headerClip">
        <path d="M0 0 H800 V30 Q400 120 0 35 Z"/>
      </clipPath>
    </defs>

    <g clip-path="url(#headerClip)">
      <rect class="world-map" x="0" y="0" width="800" height="100" fill="url(#mapGlow)" role="img" aria-label="World map showing the company's global reach"/>
    </g>
    <path d="M0 35 Q400 120 800 30" fill="none" stroke="var(--accent-green)" stroke-width="4"/>

    <polygon points="36,500 638,500 630,516 28,516" fill="var(--platform)"/>
    <rect x="28" y="516" width="602" height="10" fill="var(--platform-side)"/>

    <g class="bar">
      <rect x="41" y="346" width="55" height="170" fill="#a8d40a"/>
      <polygon points="41,346 96,346 105,335 50,335" fill="#c9e86a"/>
      <polygon points="96,346 105,335 105,505 96,516" fill="#7a9d05"/>
    </g>
    <g class="bar">
      <rect x="131" y="488" width="55" height="28" fill="#ee1111"/>
      <polygon points="131,488 186,488 195,480 140,480" fill="#f46a6a"/>
      <polygon points="186,488 195,480 195,508 186,516" fill="#a80a0a"/>
    </g>
    <g class="bar">
      <rect x="211" y="492" width="56" height="24" fill="#1aa0f2"/>
      <polygon points="211,492 267,492 275,485 219,485" fill="#74c6f6"/>
      <polygon points="267,492 275,485 275,509 267,516" fill="#0d72b3"/>
    </g>
    <g class="bar">
      <rect x="292" y="446" width="55" height="70" fill="#0d4fa8"/>
      <polygon points="292,446 347,446 356,434 301,434" fill="#5d88c8"/>
      <polygon points="347,446 356,434 356,504 347,516" fill="#083679"/>
    </g>
    <g class="bar">
      <rect x="382" y="415" width="59" height="101" fill="#9a3ad6"/>
      <polygon points="382,415 441,415 451,404 392,404" fill="#c285ea"/>
      <polygon points="441,415 451,404 451,505 441,516" fill="#6a1f9c"/>
    </g>
    <g class="bar">
      <rect x="472" y="494" width="56" height="22" fill="#ffc400"/>
      <polygon points="472,494 528,494 537,487 481,487" fill="#ffdd66"/>
      <polygon points="528,494 537,487 537,509 528,516" fill="#c49500"/>
    </g>
    <g class="bar">
      <rect x="555" y="502" width="56" height="14" fill="#08b04a"/>
      <polygon points="555,502 611,502 619,497 563,497" fill="#5fd28a"/>
      <polygon points="611,502 619,497 619,511 611,516" fill="#067a33"/>
    </g>

    <rect x="0" y="590" width="800" height="10" fill="var(--accent-green)"/>
  </svg>

  <h1 class="project-title">PROJECT TITLE HERE</h1>

  <div class="brand-tab">
    <div class="brand-mark"></div>
    <div class="brand-name">PAX</div>
  </div>

  <section class="content">
    <h2 class="content-heading">Content Heading Here</h2>
    <p class="content-body">Sub content here Sub content here Sub content here Sub content here Sub content here Sub content here Sub content here Sub content here Sub content here Sub content here Sub content here Sub content here</p>
  </section>

  <div class="photo photo-vessels" role="img" aria-label="Offshore supply vessels beside an oil rig"></div>
  <div class="photo photo-cruise" role="img" aria-label="White cruise ship at sea"></div>
  <div class="photo photo-rig" role="img" aria-label="Oil rig structure silhouetted at dusk"></div>
</div>
</body>
</html>
```